New homepage and Product page - Lumen Vq

Reason: I have narrowed it done to 3 designers and just need to get the designs revised

Industry/Entity Type

Product

```html
<!DOCTYPE html>
<html lang="en">
<head>
<meta charset="utf-8">
<title>Lumen Vq – Home</title>
<link href="https://fonts.googleapis.com/css2?family=Mulish:wght@400;600;700&family=Questrial&family=Kalam:wght@300&display=swap" rel="stylesheet">
<style>
  :root {
    --green-dark: #3f8a0c;
    --green: #5aa80f;
    --green-light: #7cc51d;
    --green-text: #4e8a1a;
    --link-green: #6aae14;
    --orange: #f08a24;
    --text: #5e5e5e;
    --text-dark: #555;
    --panel: #ecebe6;
    --footer: #e9e6e1;
    --rule: #cfcbc4;
    --white: #ffffff;
  }
  * { box-sizing: border-box; margin: 0; padding: 0; }
  html, body { width: 1200px; height: 1000px; overflow: hidden; }
  body { font-family: "Mulish", sans-serif; color: var(--text); background: var(--white); position: relative; }

  .hero { position: absolute; left: 0; top: 0; width: 1200px; height: 250px;
    background: linear-gradient(180deg, #6fba17 0%, #5aa50d 60%, #4d960a 100%); overflow: hidden; }
  .hero-intro { position: absolute; left: 119px; top: 2px; width: 450px; color: var(--white);
    font-weight: 700; font-size: 17px; line-height: 23.5px; }
  .hero-button { position: absolute; left: 120px; top: 113px; width: 176px; height: 50px;
    background: var(--orange); border: 3px solid var(--white); border-radius: 3px;
    color: var(--white); font-size: 18px; font-weight: 400; display: flex; align-items: center;
    padding-left: 15px; white-space: nowrap; }
  .hero-button span { margin-left: 14px; color: #b8450a; font-weight: 700; }
  .hero-tagline { position: absolute; left: 315px; top: 110px; font-family: "Kalam", cursive;
    font-size: 30px; color: #c9ef6a; transform: rotate(-3deg); transform-origin: left center;
    white-space: nowrap; z-index: 2; }
  .hero-product { position: absolute; left: 680px; top: 0; width: 375px; height: 200px;
    background: linear-gradient(90deg, #e9f0c4 0%, #f4d04a 40%, #f6f3ea 70%, #e8e8e0 100%); border-radius: 0 0 4px 4px; }
  .slider-arrow { position: absolute; top: 0; width: 50px; height: 20px; background: var(--green-light); }
  .slider-arrow.prev { left: 0; border-radius: 0 0 4px 0; }
  .slider-arrow.next { right: 0; border-radius: 0 0 0 4px; }
  .slider-notch { position: absolute; left: 500px; top: 234px; }

  .intro { position: absolute; left: 0; top: 300px; width: 1200px; text-align: center; }
  .intro h1 { font-family: "Questrial", sans-serif; font-weight: 400; font-size: 41px; color: var(--green-text); letter-spacing: .5px; }
  .intro p { margin: 6px auto 0; width: 860px; font-size: 22px; line-height: 30px; color: var(--text); }

  .features { position: absolute; left: 120px; top: 460px; width: 958px; height: 270px;
    border: 1px solid #e2e0da; background: linear-gradient(180deg, #ecebe6 0%, #f8f8f6 60%, #ffffff 100%); }
  .features-bar { position: absolute; left: -1px; top: -1px; width: 580px; height: 40px; background: var(--green-dark);
    color: var(--white); font-size: 21px; padding: 7px 0 0 23px; letter-spacing: .3px; }
  .feature { position: absolute; left: 22px; width: 482px; }
  .feature h3 { font-size: 17px; font-weight: 700; color: #666; padding-left: 31px; position: relative; }
  .feature h3 svg { position: absolute; left: 0; top: -3px; }
  .feature p { padding-left: 32px; font-size: 14.5px; line-height: 22px; margin-top: 4px; color: #606060; }
  .feature.natural { top: 62px; }
  .feature.science { top: 172px; }
  .features-photo { position: absolute; left: 505px; top: -28px; width: 255px; height: 297px;
    background: linear-gradient(180deg, #d9c6a0 0%, #f1d9c5 45%, #f6cdbd 100%); border-radius: 120px 120px 0 0; }
  .guarantee-seal { position: absolute; left: 696px; top: 30px; }
  .guarantee-title { position: absolute; right: 23px; top: 38px; width: 130px; text-align: right;
    font-size: 15px; font-weight: 700; line-height: 22.5px; color: #666; white-space: nowrap; }
  .guarantee-text { position: absolute; right: 23px; top: 150px; width: 190px; text-align: right;
    font-size: 14.5px; line-height: 22.5px; color: #666; white-space: nowrap; }

  .trust { position: absolute; top: 766px; }
  .trust.dose { left: 118px; }
  .trust.usa { left: 620px; }
  .trust svg { position: absolute; left: 0; top: 0; }
  .trust .copy { position: absolute; top: 5px; font-size: 13.5px; line-height: 20.5px; color: #666; }
  .trust.dose .copy { left: 88px; width: 395px; }
  .trust.usa .copy { left: 83px; width: 380px; }
  .trust h4 { font-size: 14.5px; font-weight: 700; color: #666; margin-top: -1px; }
  .trust a { color: var(--link-green); font-weight: 700; text-decoration: none; }

  .footer { position: absolute; left: 0; top: 871px; width: 1200px; height: 129px; background: var(--footer); }
  .footer-rule { position: absolute; left: 120px; top: 871px; width: 958px; height: 1px; background: var(--rule); }
  .footer-credit { position: absolute; left: 120px; top: 26px; font-size: 12px; line-height: 22px; color: #666; }
  .footer-credit strong { font-weight: 700; }
  .footer-nav { position: absolute; left: 764px; top: 35px; font-size: 12.5px; color: #999; }
  .footer-nav a { color: var(--link-green); text-decoration: none; font-weight: 600; }
  .footer-nav .sep { margin: 0 5px; }
  .social { position: absolute; left: 970px; top: 29px; display: flex; gap: 10px; }
  .social span { width: 30px; height: 30px; background: #8f8f8f; border-radius: 3px; display: block; }
</style>
</head>
<body>

<header class="hero">
  <div class="slider-arrow prev"></div>
  <div class="slider-arrow next"></div>
  <p class="hero-intro">Lumen Vq Garcinia Cambogia is made with premium garcinia cambogia that supplies 60% HCA, which is the active weight-loss component of garcinia cambogia.</p>
  <div class="hero-button">LEARN MORE <span>❯</span></div>
  <div class="hero-product" role="img" aria-label="Sliced fruit halves beside a two-bottle bonus pack of the supplement"></div>
  <div class="hero-tagline">Start Losing Weight Today!</div>
  <svg class="slider-notch" width="200" height="16" viewBox="0 0 200 16" aria-hidden="true">
    <path d="M0 16 C25 16 30 1 60 1 L140 1 C170 1 175 16 200 16 Z" fill="#fff"/>
    <rect x="73" y="9" width="14" height="6" rx="3" fill="#4e9a12"/>
    <rect x="93" y="9" width="14" height="6" rx="3" fill="#e2e2e2"/>
    <rect x="113" y="9" width="14" height="6" rx="3" fill="#e2e2e2"/>
  </svg>
</header>

<section class="intro">
  <h1>THE BEST OF NATURE &amp; SCIENCE</h1>
  <p>New Lumen Vq is line of natural, high-quality, weight-loss supplements that are scientifically formulated for better efficiency!</p>
</section>

<section class="features">
  <div class="features-bar">ALL OUR PRODUCTS ARE</div>
  <div class="feature natural">
    <h3><svg width="26" height="28" viewBox="0 0 26 28" aria-hidden="true"><path d="M2 26 C2 12 10 4 24 2 C24 16 16 24 2 26 Z" fill="#8cc63f"/><path d="M2 26 L18 9" stroke="#fff" stroke-width="1.5"/></svg>100% PURE NATURAL INGREDIENTS</h3>
    <p>Lumen Vq products are made with 100% pure natural ingredients. Unlike other products, Lumen Vq products are made with premium natural ingredients for effective results.</p>
  </div>
  <div class="feature science">
    <h3><svg width="26" height="28" viewBox="0 0 26 28" aria-hidden="true"><path d="M2 26 C2 12 10 4 24 2 C24 16 16 24 2 26 Z" fill="#8cc63f"/><path d="M2 26 L18 9" stroke="#fff" stroke-width="1.5"/></svg>SCIENTIFICALLY FORMULATED</h3>
    <p>Lumen Vq products are scientifically formulated to deliver the exact clinically tested doses that are needed to see results!</p>
  </div>
  <div class="features-photo" role="img" aria-label="Smiling woman with blond hair in a light pink top"></div>
  <svg class="guarantee-seal" width="112" height="112" viewBox="0 0 112 112" role="img" aria-label="Money back guarantee seal">
    <circle cx="56" cy="56" r="54" fill="#d99a16"/>
    <circle cx="56" cy="56" r="44" fill="#f4c12a"/>
  </svg>
  <p class="guarantee-title">Lumen Vq is<br>guaranteed to<br>work or your<br>money back</p>
  <p class="guarantee-text">Simply return it to the<br>place of purchase within<br>30 days for a refund<br>with original receipt</p>
</section>

<div class="trust dose">
  <svg width="72" height="72" viewBox="0 0 72 72" role="img" aria-label="Clinically tested dose seal">
    <circle cx="36" cy="36" r="35" fill="#5b5048"/>
    <circle cx="36" cy="36" r="25" fill="#f1ede8"/>
  </svg>
  <p class="copy">Lorem ipsum dolor sit amet, consectetur adipisicing elit, sed do eiusmod incididunt ut labore et dolore magna aliqua enim ad minim laboris nisi ut aliquip ext ... <a href="#">Find out more</a></p>
</div>

<div class="trust usa">
  <svg width="68" height="72" viewBox="0 0 68 72" role="img" aria-label="Made in USA shield">
    <path d="M2 6 L66 6 L66 40 C66 56 50 66 34 72 C18 66 2 56 2 40 Z" fill="#8a8a8a"/>
    <path d="M8 12 L60 12 L60 40 C60 53 47 61 34 66 C21 61 8 53 8 40 Z" fill="#e4e4e4"/>
  </svg>
  <div class="copy">
    <h4>Made in the USA</h4>
    Lumen Vq is manufactured in a GMP-compliant manufacturing facility to ensure 100% quality.
  </div>
</div>

<div class="footer-rule"></div>
<footer class="footer">
  <div class="footer-credit">© Copyright 2014 Corvale Studio<br>Website by <strong>Corvale Studio</strong></div>
  <nav class="footer-nav"><a href="#">Home</a><span class="sep">|</span><a href="#">Products</a><span class="sep">|</span><a href="#">Contact Us</a></nav>
  <div class="social" aria-label="Social links"><span></span><span></span><span></span></div>
</footer>

</body>
</html>
```